Rultan Staffing Full Length Retractable Office Banner

I need a design for a full-length retractable banner and A-Frame Sign for each of my offices. I have included designs that have been incorporated into a poster and tri-fold as a sample. I would like to see a colorful eyecatching banner that focuses on people. Would like to see some diversity with men and woman and different races.
Rultan Staffing is a light industrial staffing firm. www.RultanStaffing.example

Target Market(s)

Job seekers looking for employment

Industry/Entity Type

Staffing / Recruiting

Font styles to use
Other font styles liked:
• Professional yet fun

Requirements
Must have
• Eye catching design with young hip vibe.
Nice to have
• primary colors with light industrial type jobs

```html
<!DOCTYPE html>
<html lang="en">
<head>
<meta charset="utf-8">
<title>Rultan Staffing — Retractable Banner</title>
<link rel="stylesheet" href="https://fonts.googleapis.com/css2?family=Lilita+One&family=Montserrat:wght@700;800&display=swap">
<style>
  :root {
    --white: #ffffff;
    --paper: #f4f5f7;
    --red: #d8262b;
    --green: #1d7a3b;
    --gray: #8b8b8d;
    --yellow: #f3c300;
    --navy: #2c2a6b;
    --rule: #c9cad3;
    --photo-light: #e9ebee;
    --photo-mid: #b9bec6;
    --photo-warm: #c79a7e;
    --photo-denim: #6f86a6;
  }
  * { box-sizing: border-box; margin: 0; padding: 0; }
  html, body { width: 1200px; height: 3048px; overflow: hidden; background: var(--white); }
  .banner {
    position: relative;
    width: 1200px;
    height: 3048px;
    overflow: hidden;
    background: var(--white);
    font-family: "Lilita One", "Arial Black", sans-serif;
    text-align: center;
  }
  .brand {
    position: absolute;
    top: 0; left: 0; right: 0;
    height: 480px;
    display: flex;
    align-items: center;
    justify-content: center;
    gap: 40px;
    background: var(--paper);
  }
  .brand-mark {
    width: 70px; height: 70px;
    border-radius: 50%;
    background: var(--green);
  }
  .brand-name {
    font-family: "Lilita One", "Arial Black", sans-serif;
    font-size: 130px;
    color: var(--navy);
    letter-spacing: 1px;
  }
  .team-photo {
    position: absolute;
    top: 480px; left: 0;
    width: 1200px; height: 1420px;
    background:
      radial-gradient(ellipse 320px 420px at 560px 500px, var(--photo-warm), transparent 70%),
      radial-gradient(ellipse 300px 500px at 1000px 700px, var(--photo-denim), transparent 70%),
      radial-gradient(ellipse 260px 380px at 160px 650px, var(--photo-mid), transparent 70%),
      linear-gradient(180deg, var(--photo-light) 0%, #d7dadf 45%, #cfd3d9 70%, var(--white) 100%);
  }
  .team-photo::after {
    content: "";
    position: absolute;
    left: 0; right: 0; bottom: 0;
    height: 380px;
    background: linear-gradient(180deg, rgba(255,255,255,0) 0%, var(--white) 90%);
  }
  .headline { position: absolute; left: 0; right: 0; line-height: 1; }
  .line-connecting { top: 1905px; font-size: 150px; color: var(--red); }
  .people-band {
    position: absolute;
    top: 2065px; left: 80px;
    width: 1040px; height: 165px;
    background: var(--green);
    box-shadow: 0 18px 0 -6px #d9dade;
    display: flex; align-items: center; justify-content: center;
  }
  .line-people { font-size: 145px; color: var(--white); line-height: 1; }
  .line-with { top: 2285px; font-size: 125px; color: var(--gray); }
  .line-great { top: 2405px; font-size: 235px; color: var(--yellow); }
  .line-orgs { top: 2625px; font-size: 128px; color: var(--navy); }
  .divider {
    position: absolute;
    top: 2775px; left: 300px;
    width: 600px; height: 4px;
    background: var(--rule);
  }
  .line-hiring { top: 2800px; font-size: 86px; color: var(--red); letter-spacing: 1px; }
  .footer-wave { position: absolute; left: 0; bottom: 0; width: 1200px; height: 170px; }
  .footer-url {
    position: absolute;
    left: 0; right: 0; bottom: 36px;
    font-family: "Montserrat", Arial, sans-serif;
    font-weight: 800;
    font-size: 62px;
    color: var(--white);
  }
</style>
</head>
<body>
  <main class="banner">
    <header class="brand">
      <span class="brand-mark"></span>
      <span class="brand-name">Rultan Staffing</span>
    </header>

    <div class="team-photo" role="img" aria-label="Photo of a diverse, smiling team of young men and women stacking their hands together over an office desk"></div>

    <h1 class="headline line-connecting">CONNECTING</h1>
    <div class="people-band"><span class="line-people">GREAT PEOPLE</span></div>
    <p class="headline line-with">WITH</p>
    <p class="headline line-great">GREAT</p>
    <p class="headline line-orgs">ORGANIZATIONS</p>
    <div class="divider"></div>
    <p class="headline line-hiring">ALWAYS HIRING</p>

    <svg class="footer-wave" viewBox="0 0 1200 170" preserveAspectRatio="none" aria-hidden="true">
      <path d="M0 30 Q600 -25 1200 30 L1200 170 L0 170 Z" fill="var(--navy)"/>
    </svg>
    <p class="footer-url">www.RultanStaffing.example</p>
  </main>
</body>
</html>
```